Sandwich Board and Poster design promoting a medical aesthetic clinic

I am looking for a clean, modern and relaxing design promoting a medical physician-led aesthetic clinic.
Services offered are neuromodulator treatment (Dyneline) and Dermal Fillers.
Logo must be included.
Use the tag line "Refresh your look, revive your spirit."
Address is 204-205 27361 93 Ave, Surrey, K7P 2R4
604-555-0172
email - info@brightmoorskin.ca
www.brightmoorskin.ca

```html
<!DOCTYPE html>
<html lang="en">
<head>
<meta charset="utf-8">
<title>Brightmoor Skin – Posters</title>
<link href="https://fonts.googleapis.com/css2?family=Montserrat:wght@400;500;600&family=Roboto:wght@400;500;700&display=swap" rel="stylesheet">
<style>
  :root {
    --backdrop: #d2d2d2;
    --ink: #060607;
    --gold: #c9a21a;
    --gold-line: #b8960c;
    --white: #ffffff;
    --muted: #75656a;
  }
  html, body { margin: 0; padding: 0; overflow: hidden; }
  body { width: 1200px; height: 874px; background: var(--backdrop); position: relative; }
  .poster {
    position: absolute; top: 106px; width: 468px; height: 661px;
    background: var(--ink); overflow: hidden;
  }
  .poster--neuro { left: 122px; }
  .poster--fillers { left: 610px; }
  .poster__art { position: absolute; inset: 0; display: block; }
  .brand {
    position: absolute; top: 404px; left: 0; right: 0; text-align: center;
    font-family: "Montserrat", sans-serif; font-weight: 400; font-size: 21px;
    letter-spacing: 7px; color: var(--white); padding-left: 7px;
  }
  .tagline {
    position: absolute; top: 482px; left: 0; right: 0; text-align: center;
    font-family: "Montserrat", sans-serif; font-weight: 600; font-size: 20px;
    line-height: 22px; letter-spacing: 0.6px; margin: 0;
  }
  .tagline__lead { color: var(--gold); display: block; }
  .tagline__rest { color: var(--white); display: block; }
  .service {
    position: absolute; top: 553px; left: 0; right: 0;
    display: flex; align-items: center; justify-content: center; gap: 8px;
    font-family: "Roboto", sans-serif; font-weight: 500; font-size: 9.5px;
    letter-spacing: 0.9px; color: var(--muted);
  }
  .service__rule { display: block; }
  .address {
    position: absolute; top: 591px; left: 0; right: 0; text-align: center;
    font-family: "Roboto", sans-serif; font-weight: 500; font-size: 9px;
    color: var(--white); letter-spacing: 0.2px;
  }
  .contact {
    position: absolute; top: 606px; left: 0; right: 0;
    display: flex; justify-content: center; align-items: center; gap: 4px;
    font-family: "Roboto", sans-serif; font-size: 9px; color: var(--gold);
  }
  .contact__phone { font-weight: 700; }
  .contact__dot { width: 4px; height: 4px; border: 1px solid var(--gold); border-radius: 50%; margin: 0 3px; }
</style>
</head>
<body>

<section class="poster poster--neuro">
  <svg class="poster__art" width="468" height="661" viewBox="0 0 468 661">
    <defs>
      <linearGradient id="neuroPhoto" x1="0" y1="0" x2="1" y2="1">
        <stop offset="0" stop-color="#e9e3de"/>
        <stop offset="0.35" stop-color="#8fe9df"/>
        <stop offset="0.6" stop-color="#c98a63"/>
        <stop offset="1" stop-color="#a86a48"/>
      </linearGradient>
    </defs>
    <rect width="468" height="420" fill="url(#neuroPhoto)" role="img" aria-label="Photo of a client receiving a neuromodulator injection at the temple"/>
    <path d="M0,417 A262,262 0 0 1 468,417 L468,661 L0,661 Z" fill="var(--ink)"/>
    <path d="M0,417 A262,262 0 0 1 468,417" fill="none" stroke="var(--gold-line)" stroke-width="4"/>
  </svg>
  <div class="brand">BRIGHTMOOR SKIN</div>
  <h2 class="tagline"><span class="tagline__lead">REFRESH YOUR LOOK,</span><span class="tagline__rest">REVIVE YOUR SPIRIT.</span></h2>
  <div class="service">
    <svg class="service__rule" width="28" height="6"><circle cx="3" cy="3" r="2" fill="none" stroke="#555" stroke-width="0.8"/><line x1="5" y1="3" x2="28" y2="3" stroke="#555" stroke-width="0.8"/></svg>
    <span>NEUROMODULATOR TREATMENT (DYNELINE)</span>
    <svg class="service__rule" width="28" height="6"><line x1="0" y1="3" x2="23" y2="3" stroke="#555" stroke-width="0.8"/><circle cx="25" cy="3" r="2" fill="none" stroke="#555" stroke-width="0.8"/></svg>
  </div>
  <div class="address">204-205 27361 93 AVE, SURREY, K7P 2R4</div>
  <div class="contact">
    <span class="contact__phone">604-555-0172</span><span class="contact__dot"></span>
    <span>info@brightmoorskin.ca</span><span class="contact__dot"></span>
    <span>www.brightmoorskin.ca</span>
  </div>
</section>

<section class="poster poster--fillers">
  <svg class="poster__art" width="468" height="661" viewBox="0 0 468 661">
    <defs>
      <linearGradient id="fillerPhoto" x1="0" y1="0" x2="1" y2="1">
        <stop offset="0" stop-color="#3f5fd6"/>
        <stop offset="0.4" stop-color="#1a1c2c"/>
        <stop offset="0.75" stop-color="#8a5238"/>
        <stop offset="1" stop-color="#c98b68"/>
      </linearGradient>
    </defs>
    <rect width="468" height="420" fill="url(#fillerPhoto)" role="img" aria-label="Photo of gloved hands injecting dermal filler near the brow"/>
    <path d="M0,417 A262,262 0 0 1 468,417 L468,661 L0,661 Z" fill="var(--ink)"/>
    <path d="M0,417 A262,262 0 0 1 468,417" fill="none" stroke="var(--gold-line)" stroke-width="4"/>
  </svg>
  <div class="brand">BRIGHTMOOR SKIN</div>
  <h2 class="tagline"><span class="tagline__lead">REFRESH YOUR LOOK,</span><span class="tagline__rest">REVIVE YOUR SPIRIT.</span></h2>
  <div class="service">
    <svg class="service__rule" width="28" height="6"><circle cx="3" cy="3" r="2" fill="none" stroke="#555" stroke-width="0.8"/><line x1="5" y1="3" x2="28" y2="3" stroke="#555" stroke-width="0.8"/></svg>
    <span>DERMAL FILLERS</span>
    <svg class="service__rule" width="28" height="6"><line x1="0" y1="3" x2="23" y2="3" stroke="#555" stroke-width="0.8"/><circle cx="25" cy="3" r="2" fill="none" stroke="#555" stroke-width="0.8"/></svg>
  </div>
  <div class="address">204-205 27361 93 AVE, SURREY, K7P 2R4</div>
  <div class="contact">
    <span class="contact__phone">604-555-0172</span><span class="contact__dot"></span>
    <span>info@brightmoorskin.ca</span><span class="contact__dot"></span>
    <span>www.brightmoorskin.ca</span>
  </div>
</section>

</body>
</html>
```